Web Design Project

We are an online tax Continuing education provider. We provide online courses for tax preparers. We want the front end page to be user friendly and for the buyer to know exactly what they are looking at. We want a front end page to look smiliar www.larkvalefiling.com. It should have a similar feel to this one.
Our website address will be www.7782QX.com
We currently have another website that is www.LedgrUMs.com but we do not want it to look like this. We want a different look but same information.
We have a logo already which is attached. We don't have specific colors in mind for the front page but don't want it to be too busy looking. It should stand out but not too simple either.
Target Market(s)
Tax Preparers. More serious and professional but these folks are usually not tech savy. Simple, easy to use, and functional is key.
Industry/Entity Type
Education
Requirements
Must have
- Use standard HTML & CSS. NO other coding is needed.
We are looking for 5-7 pages including Home page, log in, FAQ.
Please look at our current website www.LedgrUMs.com and also www.larkvalefiling.com

```html
<!DOCTYPE html>
<html lang="en">
<head>
<meta charset="utf-8">
<title>7782QX – Tax Continuing Education</title>
<link href="https://fonts.googleapis.com/css2?family=Open+Sans:wght@400;600&family=Oswald:wght@300;600&display=swap" rel="stylesheet">
<style>
:root{
  --teal:#1f6f86;
  --teal-dark:#1c4f63;
  --text-grey:#8a8f94;
  --orange-top:#f9c25c;
  --orange-bottom:#f3ac36;
  --hero-light:#f4f4f4;
  --hero-mid:#cfd0d2;
  --band-dark:#a6a7a9;
  --section-grey:#d5d6d8;
  --content-bg:#ececec;
  --footer:#a9aaac;
  --white:#ffffff;
  --photo-main:#c9894a;
}
*{margin:0;padding:0;box-sizing:border-box}
html,body{width:788px;height:1200px;overflow:hidden}
body{position:relative;font-family:"Open Sans",sans-serif;background:var(--content-bg)}
.site-header{position:absolute;left:0;top:0;width:788px;height:94px;background:var(--white);box-shadow:0 2px 4px rgba(0,0,0,.15);z-index:2}
.brand{position:absolute;left:102px;top:58px;display:flex;align-items:center;gap:6px;font-weight:600;font-size:20px;color:var(--teal-dark)}
.brand-dot{width:14px;height:14px;border-radius:50%;background:var(--orange-bottom)}
.main-nav a{position:absolute;top:64px;font-size:10px;color:#222;text-decoration:none}
.sign-in{position:absolute;left:629px;top:62px;width:60px;height:19px;border-radius:3px;background:linear-gradient(#e6e7e8,#cfd1d3);font-size:9px;color:var(--teal-dark);display:flex;align-items:center;justify-content:center;gap:5px}
.hero{position:absolute;left:0;top:94px;width:788px;height:206px;background:linear-gradient(var(--hero-light),var(--hero-mid))}
.hero-band{position:absolute;left:0;top:300px;width:788px;height:38px;background:linear-gradient(var(--band-dark),#bdbec0)}
.tagline{position:absolute;left:98px;top:132px;width:226px;font-family:"Oswald",sans-serif;font-weight:300;font-size:15px;line-height:29.5px;letter-spacing:-.2px;color:var(--teal-dark);text-transform:uppercase;white-space:nowrap}
.tagline b{font-weight:600}
.slider-dots{position:absolute;left:98px;top:267px;display:flex;gap:4px}
.slider-dots span{width:8px;height:8px;border-radius:50%;background:#b9babc;box-shadow:inset 0 1px 2px rgba(0,0,0,.3)}
.slider-dots span.active{background:var(--white)}
.hero-photo{position:absolute;left:333px;top:127px;width:357px;height:194px;background:var(--white);box-shadow:0 3px 6px rgba(0,0,0,.35);padding:5px;z-index:1}
.hero-photo div{width:100%;height:100%;background:linear-gradient(120deg,#b8742f,var(--photo-main) 45%,#8b7a70)}
.features{position:absolute;left:0;top:338px;width:788px;height:118px;background:var(--section-grey)}
.feature{position:absolute;top:13px;width:193px;height:89px;background:linear-gradient(var(--orange-top),var(--orange-bottom));color:var(--white);padding:10px 12px}
.feature h3{font-weight:400;font-size:11.5px;line-height:18px;text-transform:uppercase}
.feature p{font-size:7.3px;line-height:12.5px;color:#4a3a1e;position:absolute;left:12px;bottom:8px}
.feature-icon{position:absolute;right:14px;top:12px;width:44px;height:34px}
.faq-title-band{position:absolute;left:0;top:456px;width:788px;height:50px;background:linear-gradient(#d9dadc,#e4e5e6)}
.faq-title{position:absolute;left:98px;top:17px;font-weight:400;font-size:11.5px;color:var(--teal)}
.faq-title small{font-size:8px;color:var(--text-grey)}
.faq-hint{position:absolute;left:98px;top:524px;width:373px;height:23px;background:var(--white);font-size:7px;color:var(--text-grey);display:flex;align-items:center;padding-left:26px}
.faq-hint svg{position:absolute;left:10px;top:7px}
.faq-item{position:absolute;left:98px;width:365px;font-size:7.2px;line-height:13.5px;color:var(--teal)}
.faq-item.open{font-weight:600;font-size:7.5px}
.faq-answer{position:absolute;left:98px;top:638px;width:365px;font-size:7.2px;line-height:13.5px;color:var(--text-grey)}
.site-footer{position:absolute;left:0;top:1166px;width:788px;height:34px;background:var(--footer);font-size:7px;color:var(--white)}
.site-footer span{position:absolute;top:12px}
.legal{color:#e8f3f6}
.social{position:absolute;left:639px;top:9px;display:flex;gap:5px}
.social i{width:13px;height:13px;border-radius:50%;background:#e1e2e3;display:block}
</style>
</head>
<body>
<header class="site-header">
  <div class="brand"><span class="brand-dot"></span>7782QX</div>
  <nav class="main-nav">
    <a style="left:364px">Home</a>
    <a style="left:430px">Courses</a>
    <a style="left:506px">FAQ</a>
    <a style="left:566px">Contact</a>
  </nav>
  <div class="sign-in">
    <svg width="6" height="8" viewBox="0 0 6 8"><circle cx="3" cy="2" r="2" fill="#1c4f63"/><rect x="0" y="4.5" width="6" height="3.5" rx="1.5" fill="#1c4f63"/></svg>
    Sign In
  </div>
</header>

<section class="hero"></section>
<div class="tagline"><b>Easy-to-understand,</b><br><b>Affordable</b> continuing education<br>at your finger tips</div>
<div class="slider-dots"><span></span><span></span><span></span><span class="active"></span></div>
<div class="hero-photo"><div role="img" aria-label="Photo of a student working on a laptop in a classroom"></div></div>
<div class="hero-band"></div>

<section class="features">
  <div class="feature" style="left:98px">
    <h3>IRS Approved<br>Provider</h3>
    <svg class="feature-icon" viewBox="0 0 44 34"><circle cx="26" cy="17" r="15" fill="#ffffff" opacity=".85"/></svg>
    <p>Click here to see our<br>approved provider link at IRS website</p>
  </div>
  <div class="feature" style="left:297px">
    <h3>Certificate of<br>Completion</h3>
    <svg class="feature-icon" viewBox="0 0 44 34"><rect x="4" y="2" width="36" height="28" fill="#fff" stroke="#8a8f94"/><rect x="9" y="7" width="26" height="18" fill="none" stroke="#c9cccf"/><line x1="13" y1="13" x2="31" y2="13" stroke="#8a8f94"/><line x1="13" y1="17" x2="27" y2="17" stroke="#8a8f94"/><circle cx="33" cy="24" r="3" fill="#e3b21f"/></svg>
    <p>IMPORTANT! All federal tax return preparers<br>must have a current year PTIN.</p>
  </div>
  <div class="feature" style="left:496px">
    <h3>Professional</h3>
    <svg class="feature-icon" viewBox="0 0 44 34"><rect x="8" y="6" width="28" height="24" fill="#f2e6c8" stroke="#8a8f94" transform="rotate(-12 22 18)"/><line x1="14" y1="26" x2="30" y2="8" stroke="#4a3a1e" stroke-width="2"/></svg>
    <p>Complete your continuing education<br>requirements now so you can concentrate<br>on servicing your tax clients.</p>
  </div>
</section>

<div class="faq-title-band"><h2 class="faq-title">FAQ's <small>(Frequently Asked Questions)</small></h2></div>

<div class="faq-hint">
  <svg width="6" height="9" viewBox="0 0 6 9"><path d="M0 0 L0 8 L2 6 L3.5 9 L4.5 8.5 L3 5.5 L6 5.5 Z" fill="#1f6f86"/></svg>
  Click on the questions below to see their corresponding answers.
</div>

<div class="faq-item" style="top:560px">1) Are we an IRS-approved provider for tax continuing education courses?</div>
<div class="faq-item" style="top:587px">2) Do I need to finish my training in one session?</div>
<div class="faq-item open" style="top:614px">3) Is the Certificate of Completion available once I finish my course?</div>
<p class="faq-answer">Yes, once you pass your exam for that course, the "Certificate of Completion" will be automatically sent to your e-mail. At that time, the certificate will be printable.</p>
<div class="faq-item" style="top:682px">4) How does the IRS know that I have completed the course?</div>
<div class="faq-item" style="top:709px">5) Does completing my hours renew my license?</div>
<div class="faq-item" style="top:736px">6) How do I know my CE hours have been reported to the IRS?</div>
<div class="faq-item" style="top:763px">7) Do you accept checks or money orders for payment?</div>
<div class="faq-item" style="top:790px">8) Is my online payment secure?</div>
<div class="faq-item" style="top:817px">9) How can I contact your company?</div>
<div class="faq-item" style="top:844px">10) Is there a refund policy?</div>
<div class="faq-item" style="top:871px">11) How long do I have to complete my course?</div>
<div class="faq-item" style="top:898px">12) I need to renew my PTIN or apply for a new PTIN. How can I do this?</div>
<div class="faq-item" style="top:925px">13) Where can I find out exactly how many continuing education hours I need?</div>
<div class="faq-item" style="top:952px">14) Do I have to reside in the United States to receive credit for the courses?</div>
<div class="faq-item" style="top:979px">15) How does our program work, i.e., how does the student take the course?</div>
<div class="faq-item" style="top:1006px">16) What is the RTRP 10-Hour CE Credit Exam Simulator Prep Course comprised of?</div>
<div class="faq-item" style="top:1034px">17) I am an inexperienced tax preparer who wishes to learn how to prepare taxes and study for the<br>RTRP Exam at the same time. Does your RTRP 10-Hour Exam Simulator Prep Course help achieve this goal?</div>
<div class="faq-item" style="top:1075px">18) How does your RTRP 10-Hour CE Credit Exam Simulator Prep Course work?</div>

<footer class="site-footer">
  <span style="left:98px">Copyright © 2012. All Rights Reserved</span>
  <span class="legal" style="left:327px">Terms &amp; Condition &nbsp;&nbsp;| &nbsp;&nbsp;Privacy Policy</span>
  <span style="left:581px">Social Media</span>
  <div class="social"><i></i><i></i><i></i></div>
  <span style="left:751px">C4</span>
</footer>
</body>
</html>
```